Church Website with Home Page and Member Sermon Library

I am in need of an updated design for our church website. This will include 4 pages (outlined below). We are a conservative, evangelical, Christian church. The site should be modern and clean, while still reflecting our conservative values. I already have a logo for our church, and I want the site to incorporate the logo, and match the logo/branding. Stock photos are allowed if needed, but I have uploaded some images of our church and would prefer those images to be used if possible. Any stock photos used should not include any people in the photos (scenery, nature, buildings, animals, etc. are fine).

The site will need 4 pages: Home, Support Us (Donate), Login, and Recording Library.

Page 1: Home
The home page should include the following sections:

- Navigation: Should include links to each section of the home page plus a "listen live" link which will take the user to a live-streaming site and a "support us" link which will take the user to a support/donate page.

- Announcements: Can be either a banner or some other design, but there needs to be some way for us to post announcements for visitors to see. I'm open for creative ideas in this section, but would like it not to take up a lot of room on the page.

- About Us: Should include address, service times (see attached document), and information about the church.

- Pastor Bio: A section that introduces our pastor and gives a short bio about our pastor. Would like this section to include a picture of our pastor. Somewhere in this section I would like to include this Bible reference: "And I will give you pastors according to mine heart, which shall feed you with knowledge and understanding. Jer 3:15 LPW"

- Articles of Faith (What We Believe): This should include several sub-sections each with a heading, body, and possibly 1 or more scripture references. I have attached a document to the brief that includes our articles of faith. Feel free to be creative with this section in how you lay these out and format them.

- Support Us: A small section that explains what kind of support someone can give and a link to a donation page. The link can say something like "Support Us" or "Donate Now".

- Contact form: A contact form that allows the visitor to send us a message. The contact form should ask for name, email, phone, and message.

- Footer: A footer that will be displayed on all pages of the site. This should include at a minimum a link to the home page (or a link to each individual section in the home page if you prefer), a link to "listen live", a link to "support us", a link to "contact us" (or you can put the contact form directly in the footer if you prefer), the address, and a "member login" link.

Page 2: Support Us
The donation page should include a form the visitor can fill out to make a donation. We will embed a third party form later. For this design, please just mock out the design with a basic form asking for name, phone, and email.

Page 3: Login
The recording library (detailed below) will require members to login with a shared numeric code before accessing the page. We need a design for a login screen. The screen should include navigation/footer just like all other pages, but the body of the login page will consist only of a form that asks the user to enter the access code and then a "login" button.

Page 4: Recording Library

The library page is a member-only page that will require a shared, numeric pass code to access. On this page, members will be able to access a filterable list of past sermons. The page by default should display most recent sermons, but should also include a search form that allows the member to filter the sermon list to find a particular sermon. The search form should allow the user to select a filter type (e.g. Speaker name, date, event, etc.) and type in a value to search. They should be able to add multiple filters and remove filters that have been added. Each sermon that is displayed in the result list should include basic information such as title, date, speaker, tags, etc. along with a download icon, and an embedded audio player where they can click a play button to stream it on-demand. Each sermon should also have clickable tags associated with it that can be used to find related sermons.
Updates

I have uploaded several images of our church. Feel free to incorporate these into your design if possible.

Target Market(s)

Church Members

Industry/Entity Type

Religion

Number of Pages Required

4 page

Font styles to use
Sans Serif

Colors

Designer to choose colors to be used in the design.

Requirements
Must have
• Must incorporate the logo (attached)
Nice to have
• Would like the design to incorporate pictures of our church (attached) instead of stock photos if possible.
Should not have
• Please avoid an overly cluttered design. Stock photos used should not include any people in the photos.

```html
<!DOCTYPE html>
<html lang="en">
<head>
<meta charset="utf-8">
<title>Cedar Hill Chapel – Home</title>
<link href="https://fonts.googleapis.com/css2?family=Cinzel:wght@400;500;600&family=Montserrat:ital,wght@0,400;0,500;0,600;1,400&display=swap" rel="stylesheet">
<style>
:root{
  --teal:#3fa9c6;
  --green:#79a86a;
  --navy:#4b6d8a;
  --ink:#2b2b2b;
  --body:#6b6b6b;
  --dark:#333333;
  --line:#dcdcdc;
  --white:#ffffff;
  --brick:#a87a62;
}
*{margin:0;padding:0;box-sizing:border-box}
html,body{width:1200px;height:4622px;overflow:hidden}
body{position:relative;background:var(--white);font-family:'Montserrat',sans-serif;color:var(--body);font-size:13px;line-height:1.6}
.abs{position:absolute}
.serif{font-family:'Cinzel',serif}
a{color:inherit;text-decoration:none}
.wordmark{font-family:'Cinzel',serif;font-weight:500;color:var(--green);text-align:center;letter-spacing:3px;line-height:1.15;display:flex;flex-direction:column;align-items:center;gap:8px}
.wordmark .mark-box{width:22px;height:22px;border:2px solid var(--green)}
.btn-pill{display:inline-flex;align-items:center;justify-content:center;gap:8px;border-radius:30px;background:var(--green);color:var(--white);font-family:'Cinzel',serif;font-weight:600;letter-spacing:.5px}
.eyebrow{font-family:'Cinzel',serif;color:var(--teal);letter-spacing:1.5px;font-size:14px}
.heading{font-family:'Cinzel',serif;color:var(--ink);font-weight:400;letter-spacing:4px}

/* hero */
.hero{left:0;top:0;width:1200px;height:648px;overflow:hidden}
.hero-photo{position:absolute;inset:0;background:linear-gradient(90deg,#fff 0%,#fff 22%,rgba(255,255,255,.6) 42%,rgba(255,255,255,0) 60%),linear-gradient(180deg,#d9dcdf 0%,#cfc9c2 20%,#b08670 45%,#9c6f58 80%,#8a7a62 100%)}
.nav{left:535px;top:50px;display:flex;align-items:center;font-size:13px;color:var(--ink);font-weight:500}
.nav a{margin-right:46px}
.nav .btn-pill{width:148px;height:42px;font-size:13px;margin-right:28px}
.nav .login{display:flex;align-items:center;gap:5px}
.hero-title{left:140px;top:256px;font-size:63px;line-height:68px;letter-spacing:6px;color:var(--ink);font-family:'Cinzel',serif}
.hero-rule{left:140px;top:414px;width:160px;height:2px;background:var(--navy)}
.hero-rule2{left:140px;top:420px;width:210px;height:1px;background:var(--teal)}
.listen{left:140px;top:452px;width:222px;height:60px;border-radius:30px;background:#f3f2ef;display:flex;align-items:center;padding-left:14px;gap:24px;font-family:'Cinzel',serif;color:var(--green);font-size:15px;font-weight:600}

/* about */
.about-text{left:572px;top:742px;width:450px}
.about-text .heading{font-size:35px;line-height:41px;margin:6px 0 12px}
.about-text p{font-size:13px;line-height:22px;margin-bottom:18px}
.about-rule{width:128px;height:2px;background:var(--teal);margin:8px 0 24px}
.service-title{font-family:'Cinzel',serif;color:var(--ink);font-weight:600;font-size:16px;letter-spacing:2px;margin-bottom:14px}
.service-list{list-style:none;font-family:'Cinzel',serif;color:var(--ink);font-size:13px;letter-spacing:1px}
.service-list li{height:33px}
.service-list span{color:var(--teal);margin-right:8px}
.service-list b{font-weight:600;margin-left:8px}

/* announcement */
.announce{left:176px;top:1318px;width:848px;height:360px}
.announce-body{left:0;top:138px;width:848px;text-align:center}
.announce-body .heading{font-size:33px;letter-spacing:3px}
.announce-body p{font-size:13px;color:var(--ink);line-height:22px;margin-top:14px}
.announce-meta{left:210px;top:250px;width:430px;display:flex;align-items:center}
.announce-meta .left{width:190px;text-align:center;padding-right:24px;font-family:'Cinzel',serif;color:var(--ink)}
.announce-meta .left div:first-child{font-size:17px;letter-spacing:2px}
.announce-meta .left div:last-child{font-size:11px;margin-top:6px;letter-spacing:1px}
.announce-meta .divider{width:1px;height:56px;background:var(--ink)}
.announce-meta .right{padding-left:22px;font-size:12px;color:var(--ink)}
.announce-meta .right div:first-child{font-family:'Cinzel',serif;letter-spacing:2px;line-height:15px}
.announce-meta .right div:last-child{font-style:italic;margin-top:6px}

/* pastor */
.pastor{left:0;top:1686px;width:1200px;height:739px;background:linear-gradient(180deg,#faf8f8 0%,#f1eeee 45%,#e4e0df 80%,#d2cecd 100%)}
.pastor-head{left:0;top:70px;width:1200px;text-align:center}
.pastor-head .heading{font-size:33px;line-height:41px;margin-top:8px;letter-spacing:3px}
.pastor-col{width:250px;font-size:13px;line-height:21px}
.pastor-col p{margin-bottom:18px}
.pastor-photo{left:465px;top:206px;width:268px;height:268px;border-radius:50%;border:6px solid var(--white);box-shadow:0 0 0 2px #cfcfcf;background:radial-gradient(circle at 50% 40%,#e9e6e1 0%,#b8a89a 50%,#3a3431 100%)}
.pastor-name{left:0;top:488px;width:1200px;text-align:center;font-family:'Cinzel',serif;color:var(--ink)}
.pastor-name small{display:block;font-size:8px;letter-spacing:1px}
.pastor-name div{font-size:16px;letter-spacing:1px}
.quote{left:0;top:560px;width:1200px;text-align:center;font-style:italic;font-size:17px;line-height:27px;color:var(--body)}
.quote-ref{left:0;top:634px;width:1200px;text-align:center;font-family:'Cinzel',serif;font-size:17px;color:var(--ink)}
.read-bio{font-family:'Cinzel',serif;color:var(--green);font-size:13px;display:inline-block;border-bottom:1px solid var(--green);padding-bottom:8px;width:110px}

/* articles */
.articles-title{left:0;top:2516px;width:1200px;text-align:center;font-size:33px}
.articles-rule{left:530px;top:2574px;width:140px;height:2px;background:var(--teal)}
.article{width:236px;font-size:12px;line-height:20px;padding-bottom:22px;border-bottom:1px solid var(--line)}
.article h3{font-family:'Cinzel',serif;font-weight:400;color:var(--ink);font-size:17px;line-height:21px;letter-spacing:1.5px;margin-bottom:14px;padding-left:16px;position:relative}
.article h3::before{content:"";position:absolute;left:0;top:8px;width:5px;height:5px;border-radius:50%;background:var(--teal)}
.article p{margin-bottom:12px}
.article u{font-style:italic}
.refs{list-style:none;font-size:10px;line-height:24px}
.refs span{color:var(--green);font-family:'Cinzel',serif;font-size:12px;margin-right:6px}
.refs i{text-decoration:underline}

/* support */
.support-head{left:0;top:3306px;width:1200px;text-align:center}
.support-head .heading{font-size:33px;line-height:46px;margin-top:6px;letter-spacing:3px}
.support-btn{left:525px;top:3448px;width:150px;height:42px;font-size:14px}
.church-photo{left:0;top:3500px;width:1200px;height:420px;background:linear-gradient(180deg,#fff 0%,#d8d9d8 12%,#b6927e 35%,#a77a63 55%,#8d7361 75%,#4e4743 90%,#333 100%)}

/* contact */
.contact{left:0;top:3800px;width:1200px;height:822px;background:linear-gradient(180deg,rgba(51,51,51,0) 0%,rgba(51,51,51,.9) 10%,var(--dark) 20%)}
.contact-head{left:0;top:3832px;width:1200px;text-align:center;color:var(--white)}
.contact-head .eyebrow{color:#e7e7e7}
.contact-head h2{font-family:'Cinzel',serif;font-weight:400;font-size:33px;letter-spacing:4px;margin-top:2px}
.field{background:var(--white);border:2px solid #e8e8e8;font-size:10px;color:var(--ink);padding:13px 16px}
.send{left:536px;top:4180px;width:138px;height:46px;font-size:15px}

/* footer */
.foot-col{font-family:'Montserrat',sans-serif;color:#d7d7d7;font-size:11px}
.foot-col h4{font-family:'Cinzel',serif;font-weight:400;color:var(--white);font-size:15px;letter-spacing:1.5px;margin-bottom:8px}
.quick a{display:block;font-size:12px;line-height:30px}
.copyright{left:98px;top:4585px;font-size:10px;color:#e0e0e0}
.socials{left:926px;top:4584px;display:flex;gap:16px}
.socials span{width:10px;height:10px;border-radius:50%;background:var(--white)}
</style>
</head>
<body>

<!-- HERO -->
<section class="abs hero">
  <div class="hero-photo" role="img" aria-label="Brick church building exterior with sign, softly faded into white on the left"></div>
  <div class="abs wordmark" style="left:140px;top:30px;width:160px;font-size:22px">
    <span class="mark-box"></span>
    <span>CEDAR HILL<br>CHAPEL</span>
  </div>
  <nav class="abs nav">
    <a href="#">Home</a>
    <a href="#">Recording Library</a>
    <a href="#" class="btn-pill">
      <svg width="16" height="16" viewBox="0 0 16 16"><circle cx="8" cy="8" r="6" fill="none" stroke="#fff" stroke-width="1.5"/><path d="M8 4v8M5.5 6.5h4a1.5 1.5 0 0 1 0 3h-3" fill="none" stroke="#fff" stroke-width="1.2"/></svg>
      SUPPORT US</a>
    <a href="#" class="login">
      <svg width="12" height="14" viewBox="0 0 12 14"><circle cx="6" cy="4" r="3" fill="#79a86a"/><path d="M0 14a6 5 0 0 1 12 0z" fill="#79a86a"/></svg>
      Login</a>
  </nav>
  <h1 class="abs hero-title">KEEP FAITH<br>ALWAYS</h1>
  <div class="abs hero-rule"></div>
  <div class="abs hero-rule2"></div>
  <a href="#" class="abs listen">
    <svg width="34" height="34" viewBox="0 0 34 34"><circle cx="17" cy="13" r="2.5" fill="#3e4e3a"/><path d="M12 8a7 7 0 0 0 0 10M22 8a7 7 0 0 1 0 10M9 5a11 11 0 0 0 0 16M25 5a11 11 0 0 1 0 16" fill="none" stroke="#3e4e3a" stroke-width="1.6"/><rect x="10" y="24" width="14" height="7" rx="1" fill="#79a86a"/></svg>
    LISTEN LIVE
  </a>
</section>

<!-- ABOUT -->
<section>
  <svg class="abs" style="left:130px;top:682px" width="420" height="580" viewBox="0 0 420 580" aria-hidden="true">
    <path d="M10 570V250Q10 110 190 5Q370 110 370 250V570" fill="none" stroke="#eeeeee" stroke-width="10"/>
    <path d="M60 250Q60 140 190 60Q320 140 320 250" fill="none" stroke="#f2f2f2" stroke-width="6"/>
    <line x1="190" y1="5" x2="190" y2="90" stroke="#f2f2f2" stroke-width="6"/>
  </svg>
  <svg class="abs" style="left:158px;top:770px" width="320" height="480" viewBox="0 0 320 480" role="img" aria-label="Arch-framed photo of the brick church wall with its sign">
    <defs><linearGradient id="archFill" x1="0" y1="0" x2="0" y2="1"><stop offset="0" stop-color="#b48a74"/><stop offset=".6" stop-color="#9c6f58"/><stop offset="1" stop-color="#8d7a5e"/></linearGradient></defs>
    <path d="M0 480V150Q0 40 160 0Q320 40 320 150V480Z" fill="url(#archFill)"/>
  </svg>
  <div class="abs about-text">
    <div class="eyebrow">ABOUT</div>
    <h2 class="heading">WELCOME TO<br>CEDAR HILL<br>CHAPEL</h2>
    <p>Ut diam tortor consectetur lacus scelerisque tortor congue viverra egestas. Tristique in consectetur leo arcu blandit diam et sed volutpat.</p>
    <p>Aliquam at commodo venenatis quis. Velit neque interdum molestie risus consectetur vestibulum a eget. Ultricies volutpat orci eros quisque ullamcorper quis est.</p>
    <div class="about-rule"></div>
    <div class="service-title">SERVICE TIME ARE</div>
    <ul class="service-list">
      <li><span>01.</span>WEDNESDAY EVENING SERVICE: <b>7:30 PM</b></li>
      <li><span>02.</span>SUNDAY SCHOOL: <b>10:00 AM</b></li>
      <li><span>03.</span>SUNDAY MORNING SERVICE: <b>11:00 AM</b></li>
      <li><span>04.</span>SUNDAY EVENING SERVICE: <b>5:30 PM</b></li>
    </ul>
  </div>
</section>

<!-- ANNOUNCEMENT -->
<section class="abs announce">
  <svg class="abs" style="left:0;top:0" width="848" height="360" viewBox="0 0 848 360" aria-hidden="true">
    <g fill="none" stroke="#4b6d8a">
      <path d="M40 55H355A70 70 0 0 0 493 55H808A28 28 0 0 0 836 83V327A28 28 0 0 0 808 355H40A28 28 0 0 0 12 327V83A28 28 0 0 0 40 55Z" stroke-width="5"/>
      <path d="M34 47H350M498 47H814A30 30 0 0 0 844 77V335A30 30 0 0 0 814 363M34 47A30 30 0 0 1 4 77V335A30 30 0 0 1 34 363" stroke-width="2" stroke="#9fb3c6"/>
    </g>
  </svg>
  <div class="abs wordmark" style="left:344px;top:6px;width:160px;font-size:17px">
    <span class="mark-box" style="width:16px;height:16px"></span>
    <span>CEDAR HILL<br>CHAPEL</span>
  </div>
  <div class="abs announce-body">
    <h2 class="heading">ANNOUNCEMENT BANNER SPOT</h2>
    <p>Ullamcorper facilisi egestas semper fames suscipit penatibus amet. Ut diam tortor<br>consectetur lacus scelerisque tortor congue viverra</p>
  </div>
  <div class="abs announce-meta">
    <div class="left"><div>ANNOUNCEMENT</div><div>FEBRUARY 16TH</div></div>
    <div class="divider"></div>
    <div class="right"><div>CEDAR HILL<br>CHAPEL</div><div>Pastor John Doe</div></div>
  </div>
</section>

<!-- PASTOR -->
<section class="abs pastor" role="img" aria-label="Softly blurred church sanctuary interior as background">
  <div class="abs pastor-head">
    <div class="eyebrow">OUR PASTOR</div>
    <h2 class="heading">A MAN OF PRAYER AND HIGH<br>SPIRITUALITY</h2>
  </div>
  <div class="abs pastor-col" style="left:170px;top:232px">
    <p>Ullamcorper facilisi egestas semper fames suscipit penatibus amet. Ut diam tortor consectetur lacus scelerisque tortor congue viverra egestas. Tristique in consectetur leo arcu blandit diam et sed volutpat.</p>
    <p>Aliquam at commodo venenatis quis. Velit neque interdum molestie risus consectetur vestibulum a eget.</p>
  </div>
  <div class="abs pastor-photo" role="img" aria-label="Portrait photo of the pastor holding a Bible"></div>
  <div class="abs pastor-name"><small>PASTOR</small><div>JOHN DOE</div></div>
  <div class="abs pastor-col" style="left:768px;top:232px">
    <p>Ut diam tortor consectetur lacus scelerisque tortor congue viverra egestas. Tristique in consectetur leo arcu blandit diam et sed volutpat.</p>
    <p>Aliquam at commodo venenatis quis. Velit neque interdum molestie risus consectetur vestibulum a eget.</p>
    <a href="#" class="read-bio">READ FULL BIO</a>
  </div>
  <p class="abs quote">“And I will give you pastors according to mine heart, which shall feed<br>you with knowledge and understanding.”</p>
  <div class="abs quote-ref">JER 3:15 LPW</div>
</section>

<!-- ARTICLES OF FAITH -->
<section>
  <h2 class="abs heading articles-title">ARTICLES OF FAITH</h2>
  <div class="abs articles-rule"></div>

  <article class="abs article" style="left:170px;top:2624px">
    <h3>THE GOD HEAD.</h3>
    <p>We believe in the God head bodily, known as the Divine Trinity. This body consist of God the father, Jesus Christ, his only begotten son and the redeemer of the world, and of the Holy Ghost, The Third person of the Divine Trinity</p>
  </article>
  <article class="abs article" style="left:170px;top:2888px">
    <h3>BAPTISM OF THE HOLY GHOST.</h3>
    <p>We believe in the baptism of the Holy Ghost as it is taught in the Bible and promised by our Lord Jesus Christ, with speaking in tongues as the Spirit gives utterance as the initial evidence. <u>Acts 2:4</u> we believe that the gift of the Holy Ghost is for all believers as the Lord promised. <u>Acts 2:17-18</u></p>
  </article>

  <article class="abs article" style="left:465px;top:2624px">
    <h3>FULL SALVATION.</h3>
    <p>We believe that Salvation is received only when a person comes to the realization that he or she is lost and separated from God and becomes full of godly sorrow, confessing their sins and true repentance, believing in the shed blood of the Lord Jesus Christ as the only sacrifice for sins. Through the blood of Christ we have:</p>
    <ul class="refs">
      <li><span>01.</span><i>Remission of sins, Matthew 26:28 Heb 9:22</i></li>
      <li><span>02.</span><i>Sanctification, Hebrews 13:12</i></li>
      <li><span>03.</span><i>Redemption, Revelations 5:9</i></li>
      <li><span>04.</span><i>Cleansing, 1 John 1:7 Rev. 1:5</i></li>
      <li><span>05.</span><i>Justification, Romans 5:9</i></li>
    </ul>
  </article>
  <article class="abs article" style="left:465px;top:3048px">
    <h3>SECOND COMING OF CHRIST.</h3>
    <p>We believe in the second coming of Jesus Christ. <u>Matthew 24:44 Luke 12:40</u></p>
  </article>

  <article class="abs article" style="left:775px;top:2624px">
    <h3>SANCTIFICATION</h3>
    <p>“Sanctify them through thy truth thy word is truth <u>St John 17:17</u>. For this is the will of God even your sanctification”</p>
    <p>We believe in a set apart life, separate from the world to Christ <u>2 Cor 6:17-18</u></p>
  </article>
  <article class="abs article" style="left:775px;top:2878px">
    <h3>DIVINE HEALING.</h3>
    <p>We believe Divine Healing to be included in the atonement of Jesus Christ our Lord, And believe that it is still for us today. <u>1 Peter 2:24 Luke 9:1-2 Mark 16-18 James 5:15</u></p>
  </article>
  <article class="abs article" style="left:775px;top:3088px;border-bottom:none">
    <h3>ETERNITY</h3>
    <p>We believe in Literal Eternity. Eternal Life for the believer and eternal death for those without Christ. <u>Revelations 21:1-27</u></p>
  </article>
</section>

<!-- SUPPORT -->
<section>
  <div class="abs support-head">
    <div class="eyebrow">SUPPORT US</div>
    <h2 class="heading">WHERE YOUR TREASURE IS, YOUR<br>HEART IS AS WELL</h2>
  </div>
  <div class="abs church-photo" role="img" aria-label="Wide photo of the brick church building with its sign"></div>
  <a href="#" class="abs btn-pill support-btn">SUPPORT US</a>
</section>

<!-- CONTACT -->
<section>
  <div class="abs contact"></div>
  <div class="abs contact-head">
    <div class="eyebrow">CONTACT US</div>
    <h2>FEEL FREE TO JOIN US</h2>
  </div>
  <div class="abs field" style="left:176px;top:3930px;width:416px;height:44px">Name *</div>
  <div class="abs field" style="left:612px;top:3930px;width:412px;height:44px">Phone *</div>
  <div class="abs field" style="left:176px;top:3989px;width:848px;height:44px">Email address *</div>
  <div class="abs field" style="left:176px;top:4044px;width:848px;height:110px">Message</div>
  <a href="#" class="abs btn-pill send">SEND US
    <svg width="18" height="10" viewBox="0 0 18 10"><path d="M0 5h16M12 1l4 4-4 4" fill="none" stroke="#fff" stroke-width="1.5"/></svg>
  </a>
</section>

<!-- FOOTER -->
<footer>
  <div class="abs foot-col" style="left:170px;top:4362px;width:264px;text-align:center">
    <h4>DONATION</h4>
    <p>Aliquam at commodo venenatis quis. Velit neque interdum molestie risus.</p>
    <a href="#" class="btn-pill" style="width:150px;height:40px;font-size:13px;margin-top:22px">SUPPORT US</a>
  </div>
  <div class="abs wordmark" style="left:480px;top:4390px;width:240px;font-size:30px">
    <span class="mark-box" style="width:28px;height:28px"></span>
    <span>CEDAR HILL<br>CHAPEL</span>
  </div>
  <div class="abs foot-col quick" style="left:816px;top:4362px">
    <h4>QUICK LINKS</h4>
    <a href="#">Home</a>
    <a href="#">Recording Library</a>
    <a href="#">Contact Us</a>
    <a href="#">Login</a>
  </div>
  <div class="abs copyright">Copyright 2023 Cedar Hill Chapel I All rights reserved</div>
  <div class="abs socials"><span></span><span></span><span></span><span></span></div>
</footer>

</body>
</html>
```